business card

Business card for new business.
Red and black corporate colors.
Card can have an Indsutrial feel to it. Feel free to add Rust, Bolted steel, or graphics as you see fit. We provide highly specialized services to the below mentioned industries.
Keep information out of corners so that if I want I can choose rounded corners.
Information
- front. name - title - phone - email
- Rear
Refining - Rail - Infrastructure - Mining - Energy
Calgary - Edmonton - Fort McMurray - Revelstoke - Vancouver

```html
<!DOCTYPE html>
<html lang="en">
<head>
<meta charset="utf-8">
<title>Ironvale business card</title>
<link rel="stylesheet" href="https://fonts.googleapis.com/css2?family=Arimo:wght@400;700&display=swap">
<style>
  :root {
    --bg: #1b1b1d;
    --card: #2a2b2d;
    --card-back: #26272a;
    --red: #e0161b;
    --grey: #8e8f91;
    --light: #b9babc;
    --emboss: #3c3d40;
    --muted: #6f7073;
  }
  * { box-sizing: border-box; margin: 0; padding: 0; }
  html, body { width: 1200px; height: 800px; overflow: hidden; background: var(--bg); }
  body { font-family: "Arimo", Arial, sans-serif; position: relative; }

  .card {
    position: absolute;
    left: 310px;
    width: 580px;
    height: 331px;
    border-radius: 4px;
  }
  .card--back { top: 46px; background: var(--card-back); }
  .card--front { top: 423px; background: var(--card); }

  .brand {
    display: flex;
    align-items: center;
    gap: 12px;
    font-weight: 700;
    letter-spacing: 2px;
  }

  .back-content {
    position: absolute;
    left: 60px; right: 60px; top: 50%;
    transform: translateY(-50%);
    display: flex;
    flex-direction: column;
    align-items: center;
    text-align: center;
  }
  .card--back .brand { font-size: 52px; color: var(--emboss); }
  .card--back .brand-mark { width: 22px; height: 22px; background: var(--emboss); }
  .back-rule { width: 100%; height: 2px; background: var(--red); margin: 26px 0 18px; }
  .sectors {
    color: var(--light);
    font-size: 15px;
    font-weight: 700;
    letter-spacing: 1.5px;
    text-transform: uppercase;
  }
  .cities {
    color: var(--muted);
    font-size: 14px;
    letter-spacing: .5px;
    margin-top: 10px;
  }
  .sep { color: var(--red); padding: 0 6px; }

  .card--front .brand {
    position: absolute;
    left: 60px; top: 60px;
    font-size: 44px;
    color: var(--light);
  }
  .card--front .brand-mark { width: 18px; height: 18px; background: var(--red); }

  .divider {
    position: absolute;
    left: 60px; right: 60px; top: 212px;
    height: 2px;
    background: var(--red);
  }

  .person { position: absolute; left: 60px; top: 160px; }
  .person-name { color: var(--red); font-size: 21px; font-weight: 700; letter-spacing: .5px; }
  .person-title { color: var(--grey); font-size: 16px; margin-top: 2px; }

  .contacts { position: absolute; left: 60px; top: 228px; list-style: none; }
  .contacts li {
    display: flex; align-items: center; gap: 10px;
    color: var(--grey); font-size: 15px; line-height: 24px;
  }
  .contacts svg { width: 14px; height: 14px; fill: var(--red); flex: none; }

  .address {
    position: absolute;
    right: 60px; top: 228px;
    text-align: right;
    color: var(--grey);
    font-size: 15px;
    font-style: normal;
    line-height: 24px;
  }
</style>
</head>
<body>

<section class="card card--back" aria-label="Card back">
  <div class="back-content">
    <div class="brand"><span class="brand-mark"></span>IRONVALE</div>
    <div class="back-rule"></div>
    <p class="sectors">Refining<span class="sep">|</span>Rail<span class="sep">|</span>Infrastructure<span class="sep">|</span>Mining<span class="sep">|</span>Energy</p>
    <p class="cities">Calgary<span class="sep">·</span>Edmonton<span class="sep">·</span>Fort McMurray<span class="sep">·</span>Revelstoke<span class="sep">·</span>Vancouver</p>
  </div>
</section>

<section class="card card--front" aria-label="Card front">
  <div class="brand"><span class="brand-mark"></span>IRONVALE</div>

  <div class="person">
    <p class="person-name">DANA KELLER</p>
    <p class="person-title">Managing Director</p>
  </div>

  <div class="divider"></div>

  <ul class="contacts">
    <li>
      <svg viewBox="0 0 24 24" aria-hidden="true"><path d="M6.6 10.8a15.1 15.1 0 0 0 6.6 6.6l2.2-2.2a1 1 0 0 1 1-.25 11.4 11.4 0 0 0 3.6.57 1 1 0 0 1 1 1V20a1 1 0 0 1-1 1A17 17 0 0 1 3 4a1 1 0 0 1 1-1h3.5a1 1 0 0 1 1 1c0 1.25.2 2.45.57 3.57a1 1 0 0 1-.25 1z"/></svg>
      (01) 4410 2287
    </li>
    <li>
      <svg viewBox="0 0 24 24" aria-hidden="true"><path d="M2 5h20v14H2z M2 5l10 8 10-8" stroke="#2a2b2d" stroke-width="1.5"/></svg>
      info@ironvale.com
    </li>
  </ul>

  <address class="address">
    PO BOX 418 Forge Lane<br>
    7th avenue Calgary, CA
  </address>
</section>

</body>
</html>
```